New letter head for Air Conditioning business

We need a new professional letter head design to suit our new re-branded air conditioning business. Our new logo is attached

```html
<!DOCTYPE html>
<html lang="en">
<head>
<meta charset="utf-8">
<title>Calvane Air Conditioning &amp; Refrigeration – Letterhead</title>
<link href="https://fonts.googleapis.com/css2?family=Lato:wght@400;700&family=Open+Sans:wght@400;600&display=swap" rel="stylesheet">
<style>
  :root {
    --green: #68c38a;
    --red: #f26b5e;
    --ink: #2f2f2f;
    --body: #4a4a4a;
    --rule: #8a8fa8;
    --paper: #ffffff;
    --faint: #ececec;
    --backdrop: #e9e9e9;
  }
  * { margin: 0; padding: 0; box-sizing: border-box; }
  html, body { width: 1040px; height: 1200px; overflow: hidden; background: var(--backdrop); }
  .letterhead {
    position: relative; width: 1040px; height: 1200px;
    background: var(--paper); overflow: hidden;
    font-family: "Open Sans", sans-serif; color: var(--body);
  }
  .top-bar { position: absolute; top: 0; height: 14px; }
  .top-bar--green { left: 0; width: 693px; background: var(--green); }
  .top-bar--red { left: 699px; right: 0; background: var(--red); }

  .brand { position: absolute; left: 90px; top: 40px; display: flex; align-items: center; gap: 16px; }
  .brand__dot { width: 76px; height: 76px; border-radius: 50%; background: var(--green); }
  .brand__name { font-family: "Open Sans", sans-serif; font-weight: 600; font-size: 46px; letter-spacing: 3px; color: var(--ink); line-height: 1; }
  .brand__tagline { margin-top: 6px; font-size: 11px; font-weight: 600; letter-spacing: 2.2px; color: var(--green); }

  .contact { position: absolute; left: 700px; top: 38px; padding-left: 20px; border-left: 2px solid var(--rule);
    font-family: "Lato", sans-serif; font-size: 19px; color: var(--ink); line-height: 22px; }
  .contact__item { display: flex; align-items: center; gap: 12px; }
  .contact__item svg { width: 16px; height: 16px; fill: var(--ink); flex: none; }

  .watermark { position: absolute; left: 690px; top: 907px; width: 380px; height: 380px; margin: -190px 0 0 -190px;
    border-radius: 50%; background: var(--faint); opacity: .6; }

  .letter { position: absolute; left: 98px; top: 236px; width: 842px; font-size: 15.5px; line-height: 27px; }
  .letter__date { margin-bottom: 14px; }
  .letter__recipient { line-height: 19px; margin-bottom: 48px; }
  .letter__greeting { margin-bottom: 26px; }
  .letter__para { text-align: justify; margin-bottom: 26px; }
  .letter__closing { margin-top: 62px; }
  .letter__signature { width: 230px; height: 30px; margin: 12px 0 10px; border-radius: 4px;
    background: linear-gradient(90deg, #e4e4e4, #f3f3f3); }
  .letter__signer { font-size: 19px; color: var(--ink); line-height: 26px; }
  .letter__role { font-size: 15.5px; }

  .footer-address { position: absolute; left: 98px; top: 1122px; font-family: "Lato", sans-serif; font-size: 18px; color: var(--ink); z-index: 2; }
  .footer-wave { position: absolute; left: 0; top: 0; width: 1040px; height: 1200px; }
</style>
</head>
<body>
<div class="letterhead">
  <div class="top-bar top-bar--green"></div>
  <div class="top-bar top-bar--red"></div>

  <header class="brand">
    <div class="brand__dot"></div>
    <div>
      <div class="brand__name">CALVANE</div>
      <div class="brand__tagline">AIR CONDITIONING &amp; REFRIGERATION</div>
    </div>
  </header>

  <div class="contact">
    <div class="contact__item">
      <svg viewBox="0 0 16 16"><path d="M3 2l3 0 1 3-2 1.5c.8 1.8 2.2 3.2 4 4L10.5 9l3 1v3c0 .6-.4 1-1 1C6.6 14 2 9.4 2 3.5 2 2.4 2.4 2 3 2z"/></svg>
      <span>044-555 0142 77</span>
    </div>
    <div class="contact__item">
      <svg viewBox="0 0 16 16"><path d="M1 3h14v10H1z M2.5 4.5L8 9l5.5-4.5v-.2H2.5z" fill-rule="evenodd"/></svg>
      <span>hello@calvaneair.com</span>
    </div>
    <div class="contact__item">
      <svg viewBox="0 0 16 16"><circle cx="8" cy="8" r="7"/></svg>
      <span>www.calvaneair.com</span>
    </div>
  </div>

  <div class="watermark"></div>

  <main class="letter">
    <p class="letter__date">Issuing Date: May 5, 2018</p>
    <p class="letter__recipient">Name Of Employee Mr. XYZABC<br>Address of Employee<br>Address Line 2 etc..</p>
    <p class="letter__greeting">Dear Mr.XYZABC</p>
    <p class="letter__para">Lorem Ipsum has been the industry's standard dummy text ever since the 1500s, when an unknown printer took a galley of type and scrambled it to make a type specimen book. It has survived not only five centuries, but also the leap into electronic typesetting, remaining essentially unchanged. It was popularised in the 1960s with the release of Printwell sheets containing Lorem Ipsum passages, and more recently with desktop publishing software like Pagecraft Studio including versions of Lorem Ipsum.</p>
    <p class="letter__para">Lorem Ipsum is simply dummy text of the printing and typesetting industry. Lorem Ipsum has been the industry's standard dummy text ever since the 1500s, when an unknown printer took a galley of type and scrambled it to make a type specimen book.</p>
    <p class="letter__para">It has survived not only five centuries, but also the leap into electronic typesetting, remaining essentially unchanged. It was popularised in the 1960s with the release of Printwell sheets containing Lorem IpsumIpsum passages.</p>
    <p class="letter__closing">Yours Sincerely</p>
    <div class="letter__signature" role="img" aria-label="Handwritten signature of Marcus Hale"></div>
    <p class="letter__signer">Marcus Hale</p>
    <p class="letter__role">Managing Director</p>
  </main>

  <svg class="footer-wave" viewBox="0 0 1040 1200" aria-hidden="true">
    <path d="M0 1172 C400 1182 800 1140 1040 1016 L1040 1200 L0 1200 Z" fill="var(--green)"/>
    <path d="M0 1146 C400 1172 800 1150 965 1062 C800 1156 400 1182 0 1164 Z" fill="var(--red)"/>
  </svg>

  <p class="footer-address">88, Harbour Road Westfield District, 30917</p>
</div>
</body>
</html>
```